Tree Pruning Website

We need a website for a tree Arborist, pruning company called Maple Crest Canopy Works. We look after all types of trees, knock down trees and prune trees. Our target market is from domestic clients to government clients and everything in between.

We would like to see the use of our main colours which are orange and green

We are not looking forward in seeing a template that we have seen before but a unique template. We have designed 5 templates ourselves and we wish for the design community to take our designs to the next level.

We have also designed a template for things that **we are not** looking for (Version 4)

To make it fair for everyone, we are also not giving out any participation payments as we have had. One winner will take all of the payment!!!

I Have attached a image of the designs and a image of a tree.

We are just looking at the PSD file been developed. We have our own team who can slice the image up into a HTML format.

Target Market(s)

Everyone who needs to cut down a tree

Industry/Entity Type

Government

Requirements
Must have
• Logo on front page
A List of our services
jQuery slider on page
Phone Number on every page

```html
<!DOCTYPE html>
<html lang="en">
<head>
<meta charset="utf-8">
<title>Maple Crest Canopy Works</title>
<link href="https://fonts.googleapis.com/css2?family=Roboto+Condensed:wght@400;700&family=Arimo:wght@400;700&display=swap" rel="stylesheet">
<style>
:root{
  --yellow:#f2c600;
  --yellow-light:#ffe680;
  --green:#5d8f10;
  --green-bright:#7cc313;
  --green-btn:#86c21a;
  --grey-btn:#bdbdbd;
  --text:#555;
  --dark:#1e1e1e;
  --olive:#b39a00;
  --pale:#f1f1ea;
  --white:#fff;
}
*{margin:0;padding:0;box-sizing:border-box}
html,body{width:1200px;height:2243px;overflow:hidden;background:var(--white)}
body{position:relative;font-family:"Arimo",Arial,sans-serif;color:var(--text)}
.abs{position:absolute}
.top-line{left:0;top:0;width:1200px;height:10px;background:var(--yellow)}
.brand{left:46px;top:50px;display:flex;align-items:center;gap:14px}
.brand-dot{width:44px;height:44px;border-radius:50%;background:var(--green)}
.brand-name{font-family:"Roboto Condensed",sans-serif;font-weight:700;font-size:30px;color:var(--green);line-height:1}
.follow{left:644px;top:30px;display:flex;align-items:center;gap:10px;font-family:"Roboto Condensed",sans-serif;font-size:24px;color:#222}
.follow span{width:38px;height:38px;border-radius:50%;background:#b8d600;display:inline-block;margin-left:2px}
.phones{left:1010px;top:24px;font-size:17px;color:#222}
.phones div{display:flex;align-items:center;gap:18px;height:44px}
.nav{left:0;top:145px;width:1200px;height:67px;background:var(--yellow);display:flex}
.nav a{position:absolute;top:0;height:67px;line-height:67px;font-family:"Roboto Condensed",sans-serif;font-size:17px;color:#333;text-decoration:none;text-align:center;transform:translateX(-50%)}
.nav .active{background:linear-gradient(#ffe680,#f5cf25);width:151px}
.slider{left:42px;top:262px;width:1146px;height:556px;background:linear-gradient(180deg,#7f9f5a 0%,#4f7a2b 45%,#3d6d1e 100%);box-shadow:0 40px 40px -30px rgba(0,0,0,.55)}
.slide-figure{left:720px;top:0;width:300px;height:556px;background:linear-gradient(#d8d8d8 0%,#ef7d23 25%,#e86a1a 60%,#445 100%);opacity:.55}
.slide-box{left:34px;top:149px;width:446px;height:262px;background:rgba(30,30,10,.72);padding:26px 30px 0}
.slide-box h1{font-family:"Roboto Condensed",sans-serif;font-weight:400;font-size:27px;color:var(--yellow);margin-bottom:18px}
.slide-box p{font-size:13.5px;line-height:19px;color:#fff;text-align:justify}
.read-more{position:absolute;right:14px;bottom:16px;background:#fff;color:#c79a00;font-size:11px;padding:7px 18px;border-radius:12px}
.dots{left:42px;top:520px;display:flex;gap:10px}
.dots i{width:12px;height:12px;border-radius:50%;background:#c9c9c9;display:block}
.dots i.on{background:var(--green-bright)}
.use h2,.panel h2,.foot h2{font-family:"Roboto Condensed",sans-serif;font-weight:400;font-size:24px;color:var(--green)}
.use{width:258px}
.use .ph{width:258px;height:157px;margin-top:17px}
.use p,.panel p{font-size:13px;line-height:19.5px;text-align:justify;color:#6a6a6a}
.use p{margin-top:26px;height:141px;overflow:hidden}
.btn{display:inline-block;width:88px;height:26px;line-height:26px;border-radius:13px;text-align:center;font-size:12px;color:#fff;background:var(--green-btn);margin-top:15px}
.btn.grey{background:var(--grey-btn)}
.band{left:0;top:1347px;width:1200px;height:520px;background:var(--pale)}
.services{left:42px;top:1389px;width:258px;height:430px;background:linear-gradient(#6eb30d,#86c41a);border-radius:4px;box-shadow:0 4px 6px rgba(0,0,0,.15)}
.services h2{height:52px;line-height:52px;text-align:center;background:linear-gradient(#fff,#c8ec6e);font-family:"Roboto Condensed",sans-serif;font-weight:400;font-size:24px;color:var(--green);border-radius:4px 4px 0 0}
.services li{list-style:none;height:44.5px;display:flex;align-items:center;padding-left:20px;gap:26px;font-size:17px;color:#fff;border-bottom:1px solid rgba(255,255,255,.18)}
.services li.on{background:#9be02a;color:#224}
.panel p{margin-top:22px}
.ph{border-radius:0}
.gallery{left:931px;top:1443px;display:grid;grid-template-columns:120px 123px;column-gap:13px;row-gap:16px}
.gallery div{height:99px;background:linear-gradient(#3f5f2a,#e7742a 55%,#3d3a33)}
.foot-band{left:0;top:1907px;width:1200px;height:296px;background:var(--olive)}
.foot h2{color:#fff;margin-bottom:22px}
.foot ul{list-style:none;font-size:13px;line-height:22px;color:#111}
.foot p{font-size:13px;line-height:22px;color:#fff;font-weight:700}
.copy{left:0;top:2203px;width:1200px;height:40px;background:var(--dark);color:#fff;font-size:13px;text-align:center;line-height:40px}
</style>
</head>
<body>
<div class="abs top-line"></div>

<div class="abs brand"><span class="brand-dot"></span><span class="brand-name">Maple Crest Canopy Works</span></div>

<div class="abs follow">Follow us : <span></span><span></span><span></span></div>

<div class="abs phones">
  <div><svg width="24" height="20" viewBox="0 0 24 20"><path d="M2 6c0-3 5-4 10-4s10 1 10 4v2h-5V6H7v2H2z" fill="#222"/><rect x="4" y="9" width="16" height="10" rx="2" fill="#222"/></svg>0855 014 220</div>
  <div><svg width="24" height="20" viewBox="0 0 24 20"><path d="M2 6c0-3 5-4 10-4s10 1 10 4v2h-5V6H7v2H2z" fill="#222"/><rect x="4" y="9" width="16" height="10" rx="2" fill="#222"/></svg>0855 014 220</div>
</div>

<nav class="abs nav">
  <a class="active" style="left:117px">HOME</a>
  <a style="left:289px">ABOUT US</a>
  <a style="left:489px">OUR SERVICES</a>
  <a style="left:701px">GET A QUOTE</a>
  <a style="left:894px">OUR WORK</a>
  <a style="left:1089px">CONTACT US</a>
</nav>

<section class="abs slider" role="img" aria-label="Arborist in orange high-visibility gear standing on a garden lawn with trees behind">
  <div class="abs slide-figure"></div>
  <div class="abs slide-box">
    <h1>MAPLE CREST CANOPY WORKS</h1>
    <p>Lorem Ipsum is simply dummy text of the printing and typesetting industry. Lorem Ipsum has been the industry's standard dummy text ever since the 1500s, when an unknown printer took a galley of type and scrambled it to make a type specimen book. It has survived not only five centuries, but also the leap into electronic typesetting, remaining essentially unchanged. It was popularised in the 1960s with the release of</p>
    <span class="read-more">READ MORE</span>
  </div>
  <div class="abs dots"><i></i><i></i><i></i><i></i><i class="on"></i></div>
</section>

<section class="abs use" style="left:42px;top:888px">
  <h2>DOMESTIC USE</h2>
  <div class="ph" role="img" aria-label="Climber pruning a tree in a backyard" style="background:linear-gradient(#8a9a5a,#a0744a)"></div>
  <p>Lorem Ipsum is simply dummy text of the printing and typesetting industry. Lorem Ipsum has been the industry's standard dummy text ever since the 1500s, when an unknown printer took a galley of type and scrambled it to make a type specimen book. It has survived not only five centuries, but also</p>
  <span class="btn">SEE MORE</span>
</section>
<section class="abs use" style="left:338px;top:888px">
  <h2>COMMERCIAL USE</h2>
  <div class="ph" role="img" aria-label="Crew feeding branches into a wood chipper" style="background:linear-gradient(#d8dcd8,#5f8a2a)"></div>
  <p>Lorem Ipsum is simply dummy text of the printing and typesetting industry. Lorem Ipsum has been the industry's standard dummy text ever since the 1500s, when an unknown printer took a galley of type and scrambled it to make a type specimen book. It has survived not only five centuries, but also</p>
  <span class="btn grey">SEE MORE</span>
</section>
<section class="abs use" style="left:633px;top:888px">
  <h2>GOVERNMENT USE</h2>
  <div class="ph" role="img" aria-label="Town street lined with buildings" style="background:linear-gradient(#8fb0d8,#8a6a5a 55%,#555)"></div>
  <p>Lorem Ipsum is simply dummy text of the printing and typesetting industry. Lorem Ipsum has been the industry's standard dummy text ever since the 1500s, when an unknown printer took a galley of type and scrambled it to make a type specimen book. It has survived not only five centuries, but also</p>
  <span class="btn grey">SEE MORE</span>
</section>
<section class="abs use" style="left:931px;top:888px">
  <h2>NON PROFITE USE</h2>
  <div class="ph" role="img" aria-label="Chainsaw cutting through a log" style="background:linear-gradient(#5f7a4a,#b0834a)"></div>
  <p>Lorem Ipsum is simply dummy text of the printing and typesetting industry. Lorem Ipsum has been the industry's standard dummy text ever since the 1500s, when an unknown printer took a galley of type and scrambled it to make a type specimen book. It has survived not only five centuries, but also</p>
  <span class="btn grey">SEE MORE</span>
</section>

<div class="abs band"></div>

<aside class="abs services">
  <h2>OUR SERVICES</h2>
  <ul>
    <li><svg width="18" height="14" viewBox="0 0 18 14"><path d="M0 5h10V0l8 7-8 7V9H0z" fill="#3e6a08"/></svg>Diagnosis</li>
    <li><svg width="18" height="14" viewBox="0 0 18 14"><path d="M0 5h10V0l8 7-8 7V9H0z" fill="#3e6a08"/></svg>Treatment</li>
    <li><svg width="18" height="14" viewBox="0 0 18 14"><path d="M0 5h10V0l8 7-8 7V9H0z" fill="#3e6a08"/></svg>Purning</li>
    <li class="on"><svg width="18" height="14" viewBox="0 0 18 14"><path d="M0 5h10V0l8 7-8 7V9H0z" fill="#222"/></svg>tree Removal</li>
    <li><svg width="18" height="14" viewBox="0 0 18 14"><path d="M0 5h10V0l8 7-8 7V9H0z" fill="#3e6a08"/></svg>Stump removal</li>
    <li><svg width="18" height="14" viewBox="0 0 18 14"><path d="M0 5h10V0l8 7-8 7V9H0z" fill="#3e6a08"/></svg>Cabeling &amp; Brancing</li>
    <li><svg width="18" height="14" viewBox="0 0 18 14"><path d="M0 5h10V0l8 7-8 7V9H0z" fill="#3e6a08"/></svg>Arborist Consults</li>
    <li><svg width="18" height="14" viewBox="0 0 18 14"><path d="M0 5h10V0l8 7-8 7V9H0z" fill="#3e6a08"/></svg>Tree Protection</li>
  </ul>
</aside>

<section class="abs panel" style="left:338px;top:1396px;width:258px">
  <h2>ABOUT US</h2>
  <p style="height:318px;overflow:hidden">"But I must explain to you how all this mistaken idea of denouncing pleasure and praising pain was born and I will give you a complete account of the system, and expound the actual teachings of the great explorer of the truth, the master-builder of human happiness. No one rejects, dislikes, or avoids pleasure itself, because it is pleasure, but because those who do not know how to pursue pleasure rationally encounter consequences that are extremely painful. Nor again is there anyone who loves or pursues or desires to obtain pain of itself, because it is pain, but because occasionally circumstances occur in which toil and pain can procure him some great pleasure. To take a trivial example,</p>
  <span class="btn">SEE MORE</span>
</section>

<section class="abs panel" style="left:633px;top:1396px;width:258px">
  <h2>OUR TEAM</h2>
  <div class="ph" role="img" aria-label="Team of six arborists standing in front of hedges" style="height:166px;margin-top:18px;background:linear-gradient(#4e6e3a,#3a5a2e 60%,#8a8a80)"></div>
  <p style="height:143px;overflow:hidden">"But I must explain to you how all this mistaken idea of denouncing pleasure and praising pain was born and I will give you a complete account of the system, and expound the actual teachings of the great explorer of the truth, the master-builder of human happiness. No one rejects, dislikes, or avoids pleasure</p>
  <span class="btn">SEE MORE</span>
</section>

<section class="abs panel" style="left:931px;top:1396px;width:256px">
  <h2>IMAGE GALLERY</h2>
</section>
<div class="abs gallery" role="img" aria-label="Six photos of arborists in orange safety gear">
  <div></div><div></div><div></div><div></div><div></div><div></div>
</div>
<span class="abs btn" style="left:933px;top:1778px">SEE MORE</span>

<div class="abs foot-band"></div>
<section class="abs foot" style="left:46px;top:1925px"><h2>QUICK LINKS</h2>
  <ul><li>Home</li><li>About us</li><li>Services</li><li>Our work</li><li>Privcy policy</li><li>Use of Terms</li></ul></section>
<section class="abs foot" style="left:338px;top:1925px"><h2>SERVICES</h2>
  <ul><li>Dignosis</li><li>Treatment</li><li>Purning</li><li>Tree Removal</li><li>Stump Removal</li><li>Cabeling &amp; Branching</li><li>Aborist Consults</li><li>Tree Protection</li></ul></section>
<section class="abs foot" style="left:633px;top:1925px;width:258px"><h2>TESTIMONIALS</h2>
  <p style="color:#111;text-align:justify;margin-top:14px">"But I must explain to you how all this mistaken idea of denouncing pleasure and praising pain was born and I will give you a complete account of the system, and expound the actual teachings of the great explorer of the truth, the master-builder of human happiness.</p>
  <p style="color:#111;font-weight:400;font-style:italic;text-align:right;margin-top:14px">25-2-2013</p></section>
<section class="abs foot" style="left:933px;top:1925px"><h2>CONTACT US</h2>
  <p style="margin-top:40px">41 Harrow Lane,<br>BRENTWOOD , WA 6153<br>Phone: 08 5550 0147<br>Fax :&nbsp; 08 5550 0192</p></section>

<footer class="abs copy">Copyright 2013 All right reserved</footer>
</body>
</html>
```